The Plate Compass

Cutting Through the Noise to What Actually Works.

Nutrition book

Target Market(s)

People looking to be or get healthy and eat right.

```html
<!DOCTYPE html>
<html lang="en">
<head>
<meta charset="utf-8">
<title>The Plate Compass – Book Cover</title>
<link rel="stylesheet" href="https://fonts.googleapis.com/css2?family=Oswald:wght@500;700&family=Montserrat:wght@600;700&display=swap">
<style>
  :root {
    --page-bg: #eef0f2;
    --blue-top: #1f74b8;
    --blue-deep: #0f5a98;
    --cyan-accent: #3fb6e8;
    --green-accent: #7cc242;
    --yellow-title: #ffd83a;
    --white: #ffffff;
    --pale-area: #e9eef2;
    --pale-area-2: #f7f9fb;
    --navy-band: #0f3a63;
    --ink: #2b3440;
    --red: #d63a32;     --red-top: #ee6a5f;
    --blue: #1d7fcb;    --blue-top2: #58a9e6;
    --green: #3e9c3a;   --green-top: #79c66a;
    --orange: #ef8a1c;  --orange-top: #f8b35a;
    --purple: #6b3aa3;  --purple-top: #9a6ccd;
    --slate: #3f4852;   --slate-top: #6e7883;
  }
  * { box-sizing: border-box; margin: 0; padding: 0; }
  html, body { width: 1200px; height: 997px; overflow: hidden; background: var(--page-bg); }
  .cover {
    position: absolute; left: 280px; top: 28px; width: 640px; height: 940px;
    overflow: hidden; background: var(--pale-area);
    box-shadow: 0 6px 24px rgba(0,0,0,.18);
  }
  .cover-bg { position: absolute; inset: 0; }
  .title {
    position: absolute; left: 0; right: 0; top: 26px; text-align: center;
    font-family: "Oswald", sans-serif; font-weight: 700; line-height: 1;
    text-transform: uppercase;
  }
  .title-top { display: block; color: var(--white); font-size: 66px; letter-spacing: 1px; }
  .title-main { display: block; color: var(--yellow-title); font-size: 96px; margin-top: 10px; letter-spacing: 1px; }
  .subtitle {
    position: absolute; left: 0; right: 0; top: 286px; text-align: center;
    font-family: "Montserrat", sans-serif; font-weight: 700; font-size: 24px;
    line-height: 1.3; color: var(--white);
  }
  .tier {
    position: absolute; display: flex; align-items: center; justify-content: center;
    font-family: "Oswald", sans-serif; font-weight: 500; font-size: 34px;
    color: var(--white); text-transform: uppercase; letter-spacing: .5px;
    border-top: 12px solid; border-radius: 3px;
    box-shadow: 0 4px 6px rgba(0,0,0,.2);
    text-shadow: 0 2px 2px rgba(0,0,0,.3);
  }
  .tier-calories    { left: 140px; width: 350px; top: 380px; height: 66px; background: var(--red);    border-color: var(--red-top); }
  .tier-protein     { left: 128px; width: 378px; top: 456px; height: 66px; background: var(--blue);   border-color: var(--blue-top2); }
  .tier-quality     { left: 116px; width: 402px; top: 526px; height: 68px; background: var(--green);  border-color: var(--green-top); }
  .tier-timing      { left: 99px;  width: 436px; top: 596px; height: 68px; background: var(--orange); border-color: var(--orange-top); }
  .tier-supplements { left: 81px;  width: 471px; top: 666px; height: 68px; background: var(--purple); border-color: var(--purple-top); }
  .tier-noise       { left: 64px;  width: 506px; top: 736px; height: 80px; background: var(--slate);  border-color: var(--slate-top); }
  .format-label {
    position: absolute; right: 72px; top: 826px;
    font-family: "Oswald", sans-serif; font-weight: 500; font-size: 16px;
    color: var(--ink); text-transform: uppercase;
  }
  .authors {
    position: absolute; left: 0; right: 0; bottom: 0; height: 72px;
    background: var(--navy-band); color: var(--white);
    display: flex; align-items: center; justify-content: center;
    font-family: "Montserrat", sans-serif; font-weight: 700; font-size: 19px;
    text-transform: uppercase; letter-spacing: .5px;
  }
</style>
</head>
<body>
  <main class="cover">
    <svg class="cover-bg" width="640" height="940" viewBox="0 0 640 940" aria-hidden="true">
      <defs>
        <linearGradient id="sky" x1="0" y1="0" x2="0" y2="1">
          <stop offset="0" stop-color="var(--blue-top)"/>
          <stop offset="1" stop-color="var(--blue-deep)"/>
        </linearGradient>
        <linearGradient id="pale" x1="0" y1="0" x2="1" y2="1">
          <stop offset="0" stop-color="var(--pale-area)"/>
          <stop offset="1" stop-color="var(--pale-area-2)"/>
        </linearGradient>
      </defs>
      <rect width="640" height="940" fill="url(#pale)"/>
      <path d="M0 0 H640 V250 C560 330 470 380 320 380 C180 380 70 360 0 350 Z" fill="url(#sky)"/>
      <path d="M640 250 C560 330 470 380 320 380 C420 390 560 350 640 280 Z" fill="var(--green-accent)"/>
      <path d="M0 350 C60 362 120 372 170 376 C110 380 50 378 0 372 Z" fill="var(--cyan-accent)"/>
    </svg>
    <div role="img" aria-label="Faint pattern of small nutrition and media icons behind the tiers" style="position:absolute;left:0;top:390px;width:640px;height:440px;background:radial-gradient(ellipse at center,rgba(255,255,255,.5),rgba(200,212,222,.35));"></div>

    <h1 class="title">
      <span class="title-top">The Plate</span>
      <span class="title-main">Compass</span>
    </h1>
    <p class="subtitle">Cutting Through the Noise<br>to What Actually Works.</p>

    <div class="tier tier-calories">Calories</div>
    <div class="tier tier-protein">Protein</div>
    <div class="tier tier-quality">Food Quality</div>
    <div class="tier tier-timing">Meal Timing</div>
    <div class="tier tier-supplements">Supplements</div>
    <div class="tier tier-noise">Noise</div>

    <p class="format-label">Nutrition Book</p>
    <footer class="authors">By John Doe, PhD / Jane Smith, MS, RDN</footer>
  </main>
</body>
</html>
```